professional business card design for technology company

We are a small technology consulting firm, specialising in consulting based around Cloud and Managed services. Our colour scheme is yellow, blue and white, as you can see in the logos. Although we are based in melbourne australia, due to the nature of our work, our clients can be located anywhere. We are looking for a clean, professional, positive look - similar to our company logo

Target Market(s)

small business

Industry/Entity Type

Business

Contact Information for Business Card

eye catching, designed to incorporate some level of raised printing. Must contain website address, phone number, name and job title

Requirements
Must have
• Logo (attached) - use of the same colour scheme

```html
<!DOCTYPE html>
<html lang="en">
<head>
<meta charset="utf-8">
<title>Nimbara – Business Card</title>
<link href="https://fonts.googleapis.com/css2?family=Exo+2:wght@400;500;600;700&display=swap" rel="stylesheet">
<style>
  :root {
    --page-bg: #e6e4e1;
    --card-bg: #ffffff;
    --ink: #4a4a4c;
    --ink-soft: #5b5b5e;
    --brand-blue: #2aa3dc;
    --brand-yellow: #f5c518;
    --band-grey: #646466;
    --on-band: #ffffff;
  }
  * { box-sizing: border-box; margin: 0; padding: 0; }
  html, body {
    width: 1200px; height: 900px; overflow: hidden;
    background: var(--page-bg);
    font-family: "Exo 2", sans-serif;
  }
  .stage {
    width: 1200px; height: 900px;
    display: flex; align-items: center; justify-content: center;
  }
  .business-card {
    position: relative;
    width: 1000px; height: 571px;
    background: var(--card-bg);
    overflow: hidden;
    box-shadow: 0 14px 40px rgba(0,0,0,0.18);
  }
  .card-swoosh {
    position: absolute; inset: 0;
    width: 100%; height: 100%;
  }
  .brand-block {
    position: absolute;
    left: 110px; top: 175px;
    display: flex; align-items: center; gap: 16px;
  }
  .brand-dot {
    width: 34px; height: 34px; border-radius: 50%;
    background: var(--brand-blue);
  }
  .brand-name {
    font-size: 82px; font-weight: 700;
    color: var(--ink);
    letter-spacing: -1px;
    line-height: 1;
  }
  .divider {
    position: absolute;
    left: 505px; top: 70px;
    width: 2px; height: 270px;
    background: var(--ink);
  }
  .contact-block {
    position: absolute;
    left: 540px; top: 72px;
    color: var(--ink-soft);
  }
  .person-name {
    font-size: 25px; font-weight: 500;
    color: var(--brand-blue);
    letter-spacing: 1px;
    text-transform: uppercase;
  }
  .person-title {
    font-size: 18px; margin-top: 2px;
  }
  .address {
    font-size: 18px; line-height: 1.35;
    margin-top: 18px;
  }
  .contact-list {
    list-style: none;
    margin-top: 22px;
    font-size: 17px;
  }
  .contact-list li {
    display: flex; align-items: center; gap: 12px;
    height: 28px;
  }
  .contact-icon { width: 16px; height: 16px; flex: none; }
  .contact-icon path, .contact-icon rect { fill: var(--brand-blue); }
  .website {
    position: absolute;
    right: 40px; bottom: 150px;
    font-size: 21px; letter-spacing: 1px;
    color: var(--on-band);
    transform: rotate(-20deg);
    transform-origin: right bottom;
  }
</style>
</head>
<body>
<main class="stage">
  <section class="business-card" aria-label="Nimbara business card">
    <svg class="card-swoosh" viewBox="0 0 1000 571" preserveAspectRatio="none" aria-hidden="true">
      <path d="M0,480 C260,540 560,500 760,380 C720,440 520,545 200,545 C120,545 50,535 0,528 Z" fill="var(--brand-blue)"/>
      <path d="M0,540 C320,575 620,520 830,360 C900,310 955,285 1000,272 L1000,571 L0,571 Z" fill="var(--band-grey)"/>
    </svg>

    <div class="brand-block">
      <span class="brand-dot"></span>
      <span class="brand-name">Nimbara</span>
    </div>

    <div class="divider"></div>

    <div class="contact-block">
      <p class="person-name">Liam Harcourt</p>
      <p class="person-title">Managing Director</p>
      <p class="address">Level 12, 40 Collins St<br>Melbourne VIC 3000</p>
      <ul class="contact-list">
        <li>
          <svg class="contact-icon" viewBox="0 0 16 16"><path d="M3.5 1 L6 1 L7 5 L5.3 6.3 C6.2 8.3 7.7 9.8 9.7 10.7 L11 9 L15 10 L15 12.5 C15 13.9 13.9 15 12.5 15 C6.7 15 1 9.3 1 3.5 C1 2.1 2.1 1 3.5 1 Z"/></svg>
          <span>03 9555 0182</span>
        </li>
        <li>
          <svg class="contact-icon" viewBox="0 0 16 16"><path d="M4.5 0.5 H11.5 A1.5 1.5 0 0 1 13 2 V14 A1.5 1.5 0 0 1 11.5 15.5 H4.5 A1.5 1.5 0 0 1 3 14 V2 A1.5 1.5 0 0 1 4.5 0.5 Z M4.6 2.5 V12.5 H11.4 V2.5 Z"/></svg>
          <span>0412 555 018</span>
        </li>
        <li>
          <svg class="contact-icon" viewBox="0 0 16 16"><rect x="4" y="1" width="8" height="5"/><rect x="1" y="6" width="14" height="7" rx="1"/><rect x="4" y="11" width="8" height="4"/></svg>
          <span>03 9555 0183</span>
        </li>
        <li>
          <svg class="contact-icon" viewBox="0 0 16 16"><path d="M1 3 H15 V4 L8 9 L1 4 Z M1 5.5 L8 10.5 L15 5.5 V13 H1 Z"/></svg>
          <span>hello@nimbara.com</span>
        </li>
      </ul>
    </div>

    <p class="website">www.nimbaracloud.com</p>
  </section>
</main>
</body>
</html>
```